Tasteful instructions for employees/guests to wash hands

Need an aesthetic visualisation of steps to wash hands.
While we would like to convey the proper steps to wash hands we also don't want to treat our staff/guests like children, rather provide a quick reminder.
Suggested sizes
16″ × 24″
11″ × 14″
A simplified version of these steps:
- Wet your hands with clean, running water (warm or cold), turn off the tap, and apply soap.
- Lather your hands by rubbing them together with the soap. Lather the backs of your hands, between your fingers, and under your nails.
- Scrub your hands for at least 20 seconds.
- Rinse your hands well under clean, running water.
- Dry your hands using a clean towel or air dry them.

```html
<!DOCTYPE html>
<html lang="en">
<head>
<meta charset="utf-8">
<title>How to HandWash?</title>
<link rel="stylesheet" href="https://fonts.googleapis.com/css2?family=Bodoni+Moda:opsz,wght@6..96,400;6..96,700&display=swap">
<style>
  :root {
    --backdrop: #f6f6f6;
    --poster: #000000;
    --ink: #ffffff;
    --sketch-light: #2a2a2a;
    --sketch-dark: #111111;
    --shadow: rgba(0, 0, 0, 0.35);
  }
  * { margin: 0; padding: 0; box-sizing: border-box; }
  html, body {
    width: 1200px;
    height: 729px;
    overflow: hidden;
    background: var(--backdrop);
  }
  .canvas {
    position: relative;
    width: 1200px;
    height: 729px;
  }
  .poster {
    position: absolute;
    left: 376px;
    top: 28px;
    width: 768px;
    height: 1152px;
    transform: scale(0.5833);
    transform-origin: top left;
    background: var(--poster);
    color: var(--ink);
    box-shadow: 10px 10px 14px var(--shadow);
    font-family: "Bodoni Moda", "Didot", serif;
  }
  .poster__rule {
    position: absolute;
    left: 22px;
    top: 20px;
    right: 26px;
    bottom: 32px;
    border: 2px solid var(--ink);
  }
  .poster__title {
    position: absolute;
    left: 0;
    right: 0;
    top: 30px;
    text-align: center;
    font-weight: 700;
    font-size: 62px;
    letter-spacing: 4px;
    line-height: 1.2;
  }
  .step__number {
    position: absolute;
    font-weight: 700;
    font-size: 86px;
    line-height: 1;
    z-index: 2;
  }
  .step__sketch {
    position: absolute;
    border-radius: 40px;
    background: radial-gradient(circle at 50% 50%, var(--sketch-light), var(--sketch-dark) 75%);
  }
  .step__text {
    position: absolute;
    font-size: 17.5px;
    letter-spacing: 2.6px;
    line-height: 23px;
    white-space: nowrap;
  }
  .step__text--right { text-align: right; right: 269px; }
  .step__text--left { left: 308px; }
</style>
</head>
<body>
<main class="canvas">
  <article class="poster">
    <div class="poster__rule"></div>
    <h1 class="poster__title">How to HandWash?</h1>

    <section class="step">
      <div class="step__sketch" style="left:186px;top:160px;width:92px;height:110px" role="img" aria-label="Line drawing of hands under running water"></div>
      <span class="step__number" style="left:160px;top:150px">1</span>
      <p class="step__text step__text--left" style="top:195px">Wet your hands with clean,<br>running water (warm or cold)</p>
    </section>

    <section class="step">
      <div class="step__sketch" style="left:520px;top:324px;width:136px;height:84px" role="img" aria-label="Line drawing of hands with soap bubbles"></div>
      <span class="step__number" style="left:608px;top:298px">2</span>
      <p class="step__text step__text--right" style="top:337px">Turn off the tap<br>and apply soap</p>
    </section>

    <section class="step">
      <div class="step__sketch" style="left:186px;top:478px;width:88px;height:96px" role="img" aria-label="Line drawing of hands rubbing together in lather"></div>
      <span class="step__number" style="left:162px;top:448px">3</span>
      <p class="step__text step__text--left" style="top:494px">Lather your hands by rubbing them<br>together with the soap</p>
    </section>

    <section class="step">
      <div class="step__sketch" style="left:532px;top:660px;width:116px;height:88px" role="img" aria-label="Line drawing of hands scrubbing the backs and fingers"></div>
      <span class="step__number" style="left:594px;top:618px">4</span>
      <p class="step__text step__text--right" style="top:655px">Lather the backs of your hands,<br>between your fingers and under your nails</p>
    </section>

    <section class="step">
      <div class="step__sketch" style="left:190px;top:794px;width:90px;height:100px" role="img" aria-label="Line drawing of hands rinsed under running water"></div>
      <span class="step__number" style="left:156px;top:786px">5</span>
      <p class="step__text step__text--left" style="top:829px">Rinse your hands well under clean,<br>running water</p>
    </section>

    <section class="step">
      <div class="step__sketch" style="left:522px;top:944px;width:104px;height:134px" role="img" aria-label="Line drawing of hands drying on a towel"></div>
      <span class="step__number" style="left:594px;top:914px">6</span>
      <p class="step__text step__text--right" style="top:982px">Dry your hands using a clean towel<br>or air dry them</p>
    </section>
  </article>
</main>
</body>
</html>
```